Business Card Design

New business card design

Target Market(s)

Residential & Commercial Property Managers

Industry/Entity Type

Plumbing Services

Contact Information for Business Card

Name - Rowan Keddle, title - Director, Phone Number - 0431 286 517, email - rowan@tbk-plumbing.com.au, Company ABN - 73 215 904 386,

Font styles to use
Sans Serif

Colors
0054AA
0677BA
7BADD7
CADEEF
E8F1F8

```html
<!DOCTYPE html>
<html lang="en">
<head>
<meta charset="UTF-8">
<title>TBK Plumbing Services – Business Card</title>
<link href="https://fonts.googleapis.com/css2?family=Montserrat:wght@300;400;600;700&display=swap" rel="stylesheet">
<style>
  :root {
    --page-bg: #e6e8eb;
    --card-dark: #1f252b;
    --card-white: #ffffff;
    --accent-blue: #2aa8e0;
    --logo-faint: #323a42;
    --text-light: #ffffff;
    --tagline-grey: #8a8580;
  }
  * { margin: 0; padding: 0; box-sizing: border-box; }
  html, body {
    width: 1200px; height: 912px; overflow: hidden;
    background: var(--page-bg);
    font-family: "Montserrat", sans-serif;
  }
  .stage {
    position: relative; width: 1200px; height: 912px;
    display: flex; flex-direction: column; align-items: center; justify-content: center; gap: 48px;
  }
  .card {
    position: relative; width: 660px; height: 377px;
    border-radius: 22px; overflow: hidden;
    box-shadow: 0 10px 28px rgba(0,0,0,0.18);
  }
  .card--back { background: var(--card-dark); }
  .card--front { background: var(--card-white); }

  .brand { position: absolute; font-weight: 400; line-height: 1; }
  .brand__word { display: block; font-size: 92px; letter-spacing: 4px; }
  .brand__tagline { display: block; font-size: 13px; letter-spacing: 9px; margin-top: 10px; }

  .card--back .brand { left: 0; right: 0; top: 118px; text-align: center; color: var(--logo-faint); }

  .card--front .brand { left: 48px; top: 100px; }
  .card--front .brand__word { color: var(--card-dark); }
  .card--front .brand__tagline { color: var(--tagline-grey); }

  .wave { position: absolute; inset: 0; width: 660px; height: 377px; }

  .contact {
    position: absolute; right: 28px; top: 116px;
    text-align: right; color: var(--text-light);
  }
  .contact__name { font-weight: 700; font-size: 24px; color: var(--accent-blue); letter-spacing: 0.3px; }
  .contact__title { font-weight: 400; font-size: 14px; margin-top: 2px; }
  .contact__line { font-weight: 400; font-size: 15px; margin-top: 14px; display: flex; justify-content: flex-end; align-items: center; gap: 8px; }
  .contact__line--abn { margin-top: 24px; }
  .contact__label { color: var(--accent-blue); font-weight: 300; }
  .contact__icon { width: 14px; height: 14px; flex: none; }
</style>
</head>
<body>
<main class="stage">
  <section class="card card--back" aria-label="Business card back">
    <div class="brand">
      <span class="brand__word">tbk</span>
      <span class="brand__tagline">plumbing services</span>
    </div>
  </section>

  <section class="card card--front" aria-label="Business card front">
    <svg class="wave" viewBox="0 0 660 377" aria-hidden="true">
      <path d="M0,362 C200,384 322,300 402,172 C462,74 522,12 600,0 L660,0 L660,377 L0,377 Z" fill="var(--card-dark)"/>
      <path d="M0,342 C200,366 312,286 388,160 C442,72 502,10 574,0" fill="none" stroke="var(--accent-blue)" stroke-width="11"/>
    </svg>

    <div class="brand">
      <span class="brand__word">tbk</span>
      <span class="brand__tagline">plumbing services</span>
    </div>

    <div class="contact">
      <div class="contact__name">Rowan Keddle</div>
      <div class="contact__title">Director</div>
      <div class="contact__line contact__line--abn"><span><span class="contact__label">ABN</span> - 73 215 904 386</span></div>
      <div class="contact__line">
        <span>0431 286 517</span>
        <svg class="contact__icon" viewBox="0 0 24 24" aria-hidden="true"><path fill="var(--accent-blue)" d="M6.6 10.8c1.4 2.8 3.8 5.1 6.6 6.6l2.2-2.2c.3-.3.7-.4 1-.2 1.1.4 2.3.6 3.6.6.6 0 1 .4 1 1V20c0 .6-.4 1-1 1C10.6 21 3 13.4 3 4c0-.6.4-1 1-1h3.5c.6 0 1 .4 1 1 0 1.3.2 2.5.6 3.6.1.3 0 .7-.2 1z"/></svg>
      </div>
      <div class="contact__line">
        <span>rowan@tbk-plumbing.com.au</span>
        <svg class="contact__icon" viewBox="0 0 24 24" aria-hidden="true"><path fill="var(--accent-blue)" d="M2 5h20v14H2z"/><path fill="none" stroke="var(--card-dark)" stroke-width="1.8" d="M2 5l10 8 10-8"/></svg>
      </div>
    </div>
  </section>
</main>
</body>
</html>
```